High end Electrical/home automation Business Card

Need a card for a high end electrical and home automation company utilising the existing logo.
Phone
Email
Website

Like black look with raised detail. Don’t necessarily need to keep colour of logo it could be made grayscale or white etc

Target Market(s)

High end clients

Contact Information for Business Card

Brightmoor Electrical

Requirements
Must have
• Logo, phone, email, website, address

High end look
Nice to have
• Black background card
Raised font
Should not have
• Lots of colour

```html
<!DOCTYPE html>
<html lang="en">
<head>
<meta charset="utf-8">
<title>Brightmoor Electrical – Business Card</title>
<link href="https://fonts.googleapis.com/css2?family=Lato:wght@300;400&display=swap" rel="stylesheet">
<style>
  :root{
    --backdrop-top:#2e2e2e;
    --backdrop-bottom:#1e1e1e;
    --card:#1b1b1b;
    --card-edge:#262626;
    --silver:#c9c9c9;
    --silver-soft:#9a9a9a;
  }
  *{margin:0;padding:0;box-sizing:border-box}
  html,body{width:1200px;height:1017px;overflow:hidden}
  body{
    background:linear-gradient(160deg,var(--backdrop-top),var(--backdrop-bottom));
    font-family:"Lato",sans-serif;
    position:relative;
  }
  .card{
    position:absolute;
    width:540px;height:308px;
    background:var(--card);
    border:1px solid var(--card-edge);
    box-shadow:0 18px 40px rgba(0,0,0,.55);
    overflow:hidden;
  }
  .card--front{left:80px;top:140px}
  .card--back{left:580px;top:560px}

  .front-brand{
    position:absolute;inset:0;
    display:flex;flex-direction:column;align-items:center;justify-content:center;gap:18px;
  }
  .front-brand__mark{width:64px;height:64px;border-radius:50%;border:5px solid var(--silver)}
  .front-brand__name{color:var(--silver);font-size:28px;font-weight:400;letter-spacing:.5px}

  .back-accent{position:absolute;left:0;top:108px;width:16px;height:26px;background:var(--silver)}
  .contact{position:absolute;left:38px;top:96px;color:var(--silver-soft);font-size:12.5px;line-height:18px}
  .contact__name{color:var(--silver);font-size:17px;line-height:24px;letter-spacing:1px;text-transform:uppercase}
  .contact__title{margin-bottom:10px}
  .contact__address{margin-bottom:10px}
  .contact__line{display:flex;align-items:center;gap:8px}
  .contact__line svg{width:11px;height:11px;fill:var(--silver-soft)}

  .back-brand{position:absolute;right:34px;top:30px;display:flex;flex-direction:column;align-items:center;gap:12px}
  .back-brand__mark{width:150px;height:150px;border-radius:50%;border:16px solid var(--silver)}
  .back-brand__name{color:var(--silver);font-size:14px;letter-spacing:.5px}
</style>
</head>
<body>
  <section class="card card--front" aria-label="Card front">
    <div class="front-brand">
      <span class="front-brand__mark"></span>
      <span class="front-brand__name">Brightmoor Electrical</span>
    </div>
  </section>

  <section class="card card--back" aria-label="Card back">
    <div class="back-brand">
      <span class="back-brand__mark"></span>
      <span class="back-brand__name">Brightmoor Electrical</span>
    </div>
    <span class="back-accent"></span>
    <div class="contact">
      <div class="contact__name">Daniel Hartley</div>
      <div class="contact__title">President</div>
      <div class="contact__address">Brightmoor Electrical LLC<br>4120 Larkspur Avenue<br>Juneau, Alaska 99801</div>
      <div class="contact__line"><svg viewBox="0 0 24 24"><path d="M6.6 10.8a15 15 0 0 0 6.6 6.6l2.2-2.2a1 1 0 0 1 1-.25 11.4 11.4 0 0 0 3.6.57 1 1 0 0 1 1 1V20a1 1 0 0 1-1 1A17 17 0 0 1 3 4a1 1 0 0 1 1-1h3.5a1 1 0 0 1 1 1c0 1.25.2 2.45.57 3.57a1 1 0 0 1-.25 1z"/></svg>555-014-2738</div>
      <div class="contact__line"><svg viewBox="0 0 24 24"><path d="M2 5h20v14H2zm2 2v.5l8 5 8-5V7z"/></svg>info@brightmoorelectrical.com</div>
      <div class="contact__line"><svg viewBox="0 0 24 24"><path d="M12 2a10 10 0 1 0 0 20 10 10 0 0 0 0-20zm0 2a8 8 0 1 1 0 16 8 8 0 0 1 0-16z"/></svg>www.brightmoorelectrical.com</div>
    </div>
  </section>
</body>
</html>
```